QP Fiduciary Website Redesign Contest

We want to refresh our website to be more insitutional, professional for an international audience. We have designed a new logo for this purpose and that has been attached. A full brand brief and positioning statement has also been attached. Please read through all the documents carefully before designing. The old website is found here: https://qp-fiduciary.example/

Target Market(s)

Actuaries and associated businesses internationally

Industry/Entity Type

professional services - actuaries

Number of Pages Required

3 page

Font styles to use
Sans Serif

Colors
0054AA
0677BA
7BADD7
CADEEF
E8F1F8
0094D4
00A9DD
6FCCEA
C7EBF8
E9F6FB
F0912C
F2A743
F7CA91
FBE8D2
FDF5EE
EE7325
F08F49
F5BC92
FAE3D3
FDF4ED
EB3D1F
EC4F4E
F09395
F8D3D4
FCEDEE

Requirements
Must have
• blues and greens to match the logo color, complimentary colors, navigation
Nice to have
• old site: https://qp-fiduciary.example/

```html
<!DOCTYPE html>
<html lang="en">
<head>
<meta charset="utf-8">
<title>QP Fiduciary — Actuarial Software</title>
<link rel="stylesheet" href="https://fonts.googleapis.com/css2?family=Krona+One&family=Figtree:wght@400;500;600;700&display=swap">
<style>
:root{
  --blue:#0a4ff0;
  --blue-deep:#0037c8;
  --aqua:#5fe3cf;
  --teal:#1aa89a;
  --orange:#f26a1b;
  --ink:#111417;
  --body:#2c3238;
  --card-a:#e6fbf8;
  --card-b:#e4ebfb;
  --footer:#151515;
  --white:#ffffff;
}
*{margin:0;padding:0;box-sizing:border-box}
html,body{width:1200px;height:3657px;overflow:hidden;background:var(--white)}
body{position:relative;font-family:"Figtree",sans-serif;color:var(--body)}
.abs{position:absolute}
.heading{font-family:"Krona One",sans-serif;color:var(--ink);text-transform:uppercase;text-align:center;letter-spacing:1px}
.center{left:0;width:1200px;text-align:center}

/* header */
.site-header{position:absolute;top:0;left:0;width:1200px;height:98px;background:#fff;border-bottom:1px solid #cfe0ea;z-index:3}
.brand{position:absolute;left:50px;top:30px;font-family:"Figtree",sans-serif;font-weight:500;font-size:30px;letter-spacing:3px;color:#1b1f24}
.nav{position:absolute;top:42px;left:427px;display:flex;gap:28px;font-size:12.5px;font-weight:600;letter-spacing:.6px;color:#1b2a3a}
.nav .active{color:var(--orange)}
.login{position:absolute;left:1003px;top:30px;width:140px;height:38px;border-radius:19px;background:var(--orange);color:#fff;font-size:12.5px;font-weight:700;display:flex;align-items:center;justify-content:center;letter-spacing:.5px}

/* hero */
.hero{position:absolute;top:98px;left:0;width:1200px;height:600px}
.hero-title{top:190px;font-size:34px;line-height:51px}
.hero-sub{top:356px;font-size:14.5px;line-height:27px;color:#1a2a30}
.btn{position:absolute;display:flex;align-items:center;justify-content:center;border-radius:26px;font-family:"Krona One",sans-serif;font-size:12.5px;letter-spacing:.5px}
.btn-light{left:391px;top:431px;width:418px;height:51px;background:#fff;color:var(--orange)}
.btn-orange{background:var(--orange);color:#fff}

/* overview */
.section-title{font-size:32px}
.overview-text{top:858px;font-size:14.5px;line-height:26px}
.step{position:absolute;font-family:"Krona One",sans-serif;font-size:20px;color:var(--ink)}
.step-icon{position:absolute;width:72px;height:72px;border-radius:50%;background:radial-gradient(circle at 35% 30%,#2aa9ff,#0a4ff0);box-shadow:0 4px 10px rgba(10,79,240,.3)}
.hub-brand{position:absolute;left:0;width:1200px;top:1123px;text-align:center;font-weight:500;font-size:22px;letter-spacing:2px;color:#1b1f24}

/* solutions */
.sol-card{position:absolute;top:1527px;width:291px;height:295px;border-radius:14px;background:linear-gradient(135deg,var(--card-a),var(--card-b));text-align:center}
.sol-icon{width:58px;height:54px;margin:36px auto 0;border-radius:8px;background:linear-gradient(135deg,#1ec6c4,#1e5be8);opacity:.8}
.sol-card h3{margin-top:26px;font-size:18px;font-weight:700;color:var(--ink)}
.sol-card p{margin:16px 22px 0;font-size:14px;line-height:26.5px;color:#3a3f45}
.sol-card a{display:block;margin-top:14px;font-size:14px;color:#1e55e6;text-decoration:underline;font-weight:500}

/* characteristics */
.band{position:absolute;top:1898px;left:0;width:1200px;height:445px;background:var(--blue)}
.band .heading{color:#fff}
.char{position:absolute;top:2073px;width:260px;text-align:center}
.char-ring{position:relative;width:100px;height:100px;margin:0 auto;border-radius:50%;background:#fff}
.char-ring .art{position:absolute;left:24px;top:24px;width:52px;height:52px;border-radius:10px;background:linear-gradient(135deg,#9fd9ff,#2a6df0);opacity:.7}
.char-ring .num{position:absolute;right:-4px;top:-2px;width:24px;height:24px;border-radius:50%;background:var(--orange);color:#fff;font-size:11px;font-weight:600;display:flex;align-items:center;justify-content:center;border:2px solid #fff}
.char p{margin-top:20px;font-size:17.5px;font-weight:600;line-height:26px;color:#dfeaff}

/* articles */
.art-card{position:absolute;top:2495px;width:300px;height:131px;border-radius:12px;background:linear-gradient(135deg,var(--card-a),var(--card-b));text-align:center}
.art-card .tag{margin-top:24px;font-size:14px;font-weight:600}
.art-card h4{margin-top:10px;font-size:16px;font-weight:500;line-height:26px;color:var(--ink)}
.art-card .go{position:absolute;left:138px;top:108px;width:22px;height:22px;border-radius:50%;background:#1e55e6}
.go svg{display:block}

/* cta */
.cta{position:absolute;left:169px;top:2814px;width:861px;height:350px;border-radius:85px;background:linear-gradient(110deg,#0a4ff0 20%,#1a73d8 55%,#18a28a 100%)}
.cta .heading{color:#fff;font-size:32px;line-height:43px}
.cta p{position:absolute;left:0;width:861px;top:168px;text-align:center;font-size:17px;line-height:30px;color:#fff;font-weight:500}

/* footer */
.footer{position:absolute;top:3250px;left:0;width:1200px;height:407px;background:var(--footer);color:#e6e6e6}
.footer .brand{left:108px;top:80px;color:#fff;font-size:32px}
.social{position:absolute;left:108px;top:158px;width:29px;height:29px;border-radius:50%;border:2px solid #fff}
.fcol{position:absolute;top:78px}
.fcol h5{font-family:"Krona One",sans-serif;font-size:17px;color:#fff;letter-spacing:.5px;margin-bottom:16px}
.fcol li{list-style:none;font-size:15px;height:34px;display:flex;align-items:center;gap:10px}
.contact-row{position:absolute;left:906px;display:flex;align-items:center;gap:14px;font-size:15px;line-height:27px}
.contact-ico{width:32px;height:32px;border-radius:50%;background:#fff;flex:none;display:flex;align-items:center;justify-content:center}
.divider{position:absolute;left:110px;top:321px;width:980px;height:1px;background:#4a4a4a}
.copy{position:absolute;left:0;width:1200px;top:358px;text-align:center;font-size:15px;color:#f2f2f2}
</style>
</head>
<body>

<header class="site-header">
  <div class="brand">QP FIDUCIARY</div>
  <nav class="nav">
    <span class="active">HOME</span><span>PLATFORM</span><span>SOLUTIONS</span><span>INSIGHTS</span><span>COMPANY</span><span>CONTACT</span>
  </nav>
  <div class="login">CLIENT LOGIN</div>
</header>

<section class="hero">
  <svg width="1200" height="600" viewBox="0 0 1200 600" aria-hidden="true">
    <defs>
      <linearGradient id="heroBg" x1="0" y1="0" x2="1" y2="0.6">
        <stop offset="0" stop-color="#2f7fe6"/>
        <stop offset="0.35" stop-color="#38b6e8"/>
        <stop offset="0.7" stop-color="#5fe0d2"/>
        <stop offset="1" stop-color="#42c6ef"/>
      </linearGradient>
      <linearGradient id="heroInner" x1="0" y1="0" x2="1" y2="1">
        <stop offset="0" stop-color="#6ff0d6"/>
        <stop offset="0.6" stop-color="#5fd6e0"/>
        <stop offset="1" stop-color="#2fb6cf"/>
      </linearGradient>
    </defs>
    <rect width="1200" height="600" fill="url(#heroBg)"/>
    <path d="M0,600 L0,400 C60,260 160,230 190,230 C60,330 60,470 300,530 C600,610 950,560 1200,420 L1200,600 Z" fill="#fff"/>
    <path d="M0,400 C40,300 120,245 190,230 C90,320 90,450 330,515 C620,590 960,540 1200,420 C1000,560 700,620 430,598 C150,575 0,500 0,400 Z" fill="var(--blue)"/>
    <path d="M190,230 C300,150 560,120 760,150 C980,185 1150,260 1200,330 L1200,420 C960,540 620,590 330,515 C90,450 90,320 190,230 Z" fill="url(#heroInner)" opacity=".95"/>
  </svg>
  <h1 class="abs heading center hero-title" style="top:92px">Actuarial Software for<br>Structured, Auditable Financial<br>Analysis</h1>
  <p class="abs center hero-sub" style="top:258px">Software that translates actuarial methodologies into disciplined decision-ready analytical tools<br>across diverse regulatory environments</p>
  <div class="btn btn-light" style="top:333px">REQUEST A TECHNICAL WALKTHROUGH</div>
</section>

<h2 class="abs heading center section-title" style="top:788px">Platform Overview</h2>
<p class="abs center overview-text">QP Fiduciary develops modular actuarial software designed to support reserving, valuation, pricing, and risk<br>analysis workflows across diverse regulatory environments.</p>

<svg class="abs" style="left:400px;top:936px" width="400" height="400" viewBox="0 0 400 400" aria-hidden="true">
  <defs>
    <linearGradient id="ring" x1="0" y1="0" x2="0" y2="1">
      <stop offset="0" stop-color="#3a6ef0"/><stop offset="1" stop-color="#38c9a6"/>
    </linearGradient>
  </defs>
  <circle cx="200" cy="200" r="185" fill="none" stroke="url(#ring)" stroke-width="1.5"/>
  <circle cx="200" cy="200" r="142" fill="#fff" stroke="#3a6ef0" stroke-width="1.5"/>
</svg>
<div class="hub-brand">QP FIDUCIARY</div>

<div class="step-icon" role="img" aria-label="Output icon" style="left:387px;top:992px"></div>
<div class="step-icon" role="img" aria-label="Input icon" style="left:728px;top:992px"></div>
<div class="step-icon" role="img" aria-label="Review icon" style="left:394px;top:1191px"></div>
<div class="step-icon" role="img" aria-label="Analysis icon" style="left:736px;top:1191px"></div>
<div class="step" style="left:234px;top:1016px">4) OUTPUT</div>
<div class="step" style="left:816px;top:1016px">1) INPUT</div>
<div class="step" style="left:240px;top:1214px">3) REVIEW</div>
<div class="step" style="left:825px;top:1214px">2) ANALYSIS</div>

<h2 class="abs heading center section-title" style="top:1432px">Core Solutions</h2>
<div class="sol-card" style="left:111px">
  <div class="sol-icon" role="img" aria-label="Reserving icon"></div>
  <h3>Reserving &amp; Valuation</h3>
  <p>Software supporting structured reserving workflows and financial reporting across jurisdictions.</p>
  <a>Read More</a>
</div>
<div class="sol-card" style="left:454px">
  <div class="sol-icon" role="img" aria-label="Pricing icon"></div>
  <h3>Pricing</h3>
  <p>Models supporting insurance and reinsurance pricing based on actuarial methodologies.</p>
  <a>Read More</a>
</div>
<div class="sol-card" style="left:797px">
  <div class="sol-icon" role="img" aria-label="Risk management icon"></div>
  <h3>Enterprise Risk Management</h3>
  <p>Software supporting reinsurance optimization andcapital modeling.</p>
  <a>Read More</a>
</div>

<section class="band">
  <h2 class="abs heading center section-title" style="top:70px">Platform Characteristics</h2>
  <svg class="abs" style="left:0;top:0" width="1200" height="445" aria-hidden="true">
    <path d="M253,240 C320,250 380,240 414,215 M514,220 C570,250 620,290 684,258 M784,216 C830,190 880,200 962,262" fill="none" stroke="#9fc0ff" stroke-width="1.5" stroke-dasharray="3 4"/>
  </svg>
</section>
<div class="char" style="left:73px"><div class="char-ring"><div class="art" role="img" aria-label="Workflow icon"></div><div class="num">01</div></div><p>Structured workflows<br>suitable for<br>multi-jurisdictional review</p></div>
<div class="char" style="left:334px"><div class="char-ring"><div class="art" role="img" aria-label="Assumptions icon"></div><div class="num">02</div></div><p>Transparent assumptions<br>and methodological<br>clarity</p></div>
<div class="char" style="left:604px"><div class="char-ring"><div class="art" role="img" aria-label="Scenario analysis icon"></div><div class="num">03</div></div><p>Comparative<br>scenario analysis</p></div>
<div class="char" style="left:882px"><div class="char-ring"><div class="art" role="img" aria-label="Professional judgment icon"></div><div class="num">04</div></div><p style="margin-top:24px">Supports professional<br>judgment rather than<br>replacing it</p></div>

<h2 class="abs heading center section-title" style="top:2404px">Recent Articles</h2>
<div class="art-card" style="left:114px"><div class="tag" style="color:#1e55e6">Methodology</div><h4>Methodological perspectives<br>in actuarial reserving</h4><div class="go"><svg width="22" height="22"><path d="M6,11 H15 M11,7 L15,11 L11,15" stroke="#fff" stroke-width="2" fill="none"/></svg></div></div>
<div class="art-card" style="left:450px"><div class="tag" style="color:var(--teal)">Governance</div><h4>Governance considerations<br>in multi-jurisdictional analysis</h4><div class="go"><svg width="22" height="22"><path d="M6,11 H15 M11,7 L15,11 L11,15" stroke="#fff" stroke-width="2" fill="none"/></svg></div></div>
<div class="art-card" style="left:788px"><div class="tag" style="color:#1e55e6">Practice</div><h4>Observations on actuarial<br>practice in emerging markets</h4><div class="go"><svg width="22" height="22"><path d="M6,11 H15 M11,7 L15,11 L11,15" stroke="#fff" stroke-width="2" fill="none"/></svg></div></div>
<div class="btn btn-orange" style="left:503px;top:2681px;width:194px;height:50px">READ INSIGHTS</div>

<section class="cta">
  <h2 class="abs heading" style="left:0;width:861px;top:56px">Interested in exploring<br>the platform?</h2>
  <p>Schedule a technical walkthrough with our team to understand how QP<br>Fiduciary can support your actuarial workflows.</p>
  <div class="btn btn-orange" style="left:231px;top:241px;width:400px;height:51px">REQUEST A TECHNICAL WALKTHROUGH</div>
</section>

<footer class="footer">
  <div class="brand">QP FIDUCIARY</div>
  <div class="social" role="img" aria-label="Social profile link"></div>
  <div class="fcol" style="left:473px">
    <h5>QUICK LINKS</h5>
    <ul><li>➔ Home</li><li>➔ Platform</li><li>➔ Solutions</li><li>➔ Insights</li><li>➔ Contact</li></ul>
  </div>
  <div class="fcol" style="left:697px">
    <h5>HELP LINKS</h5>
    <ul><li>➔ FAQ</li><li>➔ Terms of use</li><li>➔ Privacy Policy</li><li>➔ Support Links</li><li>➔ Conditions</li></ul>
  </div>
  <div class="fcol" style="left:906px"><h5>CONTACT US</h5></div>
  <div class="contact-row" style="top:118px"><span class="contact-ico"><svg width="16" height="18" viewBox="0 0 16 18"><path d="M8,1 C4,1 1.5,4 1.5,7 C1.5,11 8,17 8,17 C8,17 14.5,11 14.5,7 C14.5,4 12,1 8,1 Z" fill="#151515"/><circle cx="8" cy="7" r="2.3" fill="#fff"/></svg></span><span>QP Fiduciary<br>United States</span></div>
  <div class="contact-row" style="top:186px"><span class="contact-ico"><svg width="16" height="16" viewBox="0 0 16 16"><path d="M3,1 L6,1 L7,5 L5,6.5 C6,9 7,10 9.5,11 L11,9 L15,10 L15,13 C15,14 14,15 13,15 C6,14.5 1.5,10 1,3 C1,2 2,1 3,1 Z" fill="#151515"/></svg></span><span>+1 555 010 0199</span></div>
  <div class="contact-row" style="top:238px"><span class="contact-ico"><svg width="16" height="12" viewBox="0 0 16 12"><rect x="0.5" y="0.5" width="15" height="11" rx="1.5" fill="#151515"/><path d="M1,1.5 L8,7 L15,1.5" stroke="#fff" stroke-width="1.3" fill="none"/></svg></span><span>info@qp-fiduciary.example</span></div>
  <div class="divider"></div>
  <div class="copy">Copyrights2026.QP Fiduciary.All Rights Reserved</div>
</footer>

</body>
</html>
```